innovative design Cafe Menu

looking for an innovative design for a food menu for a coffee shop and take away restaurant.

Target Market(s)

Canada

Requirements
Must have
• innovative design and easy to navigate and reading

```html
<!DOCTYPE html>
<html lang="en">
<head>
<meta charset="utf-8">
<title>Cafe Menu</title>
<link href="https://fonts.googleapis.com/css2?family=Bitter:wght@400;600;700&display=swap" rel="stylesheet">
<style>
:root{
  --band:#4ea246;
  --forest:#0b4a22;
  --amber:#f2a72a;
  --dish:#3f9b3d;
  --ink:#1f1f1f;
  --paper:#ffffff;
}
*{margin:0;padding:0;box-sizing:border-box}
html,body{width:1200px;height:849px;overflow:hidden;background:var(--paper)}
.menu{position:relative;width:1200px;height:849px;overflow:hidden;font-family:"Bitter",serif;color:var(--ink)}
.art{position:absolute;top:0;left:0}
.column{position:absolute}
.col-left{left:22px;top:174px;width:356px}
.col-mid{left:422px;top:279px;width:356px}
.col-right{left:822px;top:35px;width:356px}
.band{background:var(--band);color:#fff;font-weight:700;font-size:14px;height:23px;line-height:23px;padding-left:8px}
.list{padding:6px 0 0 8px}
.item{margin-bottom:10px}
.item-head{display:flex;align-items:baseline;font-size:14.4px;line-height:16px}
.item-name{color:var(--dish);font-weight:600;white-space:nowrap}
.leader{flex:1;border-bottom:1.2px dotted #333;margin:0 4px;transform:translateY(-3px)}
.price{font-size:13.2px;white-space:nowrap}
.item-desc{font-size:12px;line-height:15.8px;margin-top:1px}
.wraps{margin-top:18px}
.platter{margin-top:6px}
</style>
</head>
<body>
<main class="menu">
  <svg class="art" width="1200" height="849" viewBox="0 0 1200 849">
    <defs>
      <linearGradient id="wingsTone" x1="0" y1="0" x2="1" y2="1">
        <stop offset="0" stop-color="#c9692c"/><stop offset="0.5" stop-color="#d98a4e"/><stop offset="1" stop-color="#d9cfc6"/>
      </linearGradient>
      <linearGradient id="platterTone" x1="0" y1="0" x2="1" y2="1">
        <stop offset="0" stop-color="#8a4a2a"/><stop offset="0.5" stop-color="#c9772f"/><stop offset="1" stop-color="#3e5a2a"/>
      </linearGradient>
      <radialGradient id="soupTone"><stop offset="0" stop-color="#d98a3a"/><stop offset="1" stop-color="#6e3a2a"/></radialGradient>
      <radialGradient id="saladTone"><stop offset="0" stop-color="#c23a3a"/><stop offset="0.6" stop-color="#4d8a3a"/><stop offset="1" stop-color="#e9e9e9"/></radialGradient>
      <radialGradient id="wrapTone"><stop offset="0" stop-color="#8a5030"/><stop offset="0.6" stop-color="#e8dcc4"/><stop offset="1" stop-color="#ffffff"/></radialGradient>
    </defs>
    <path role="img" aria-label="Photo of buffalo chicken wings with dips" fill="url(#wingsTone)"
      d="M0 0 H548 C520 60 500 130 440 160 C380 190 300 150 230 165 C150 182 80 200 0 205 Z"/>
    <path class="swoosh" fill="var(--forest)" d="M0 0 H265 C210 30 150 40 100 80 C60 110 40 150 0 180 Z"/>
    <path fill="none" stroke="var(--amber)" stroke-width="2.5" d="M0 120 C60 90 90 30 190 20 C220 17 240 8 255 0"/>
    <path fill="none" stroke="#fff" stroke-width="1.5" d="M0 140 C70 110 110 40 220 25 C245 20 262 10 272 0"/>

    <circle cx="666" cy="138" r="92" fill="var(--band)"/>
    <circle role="img" aria-label="Photo of chicken enchilada soup" cx="666" cy="138" r="85" fill="url(#soupTone)"/>
    <circle cx="741" cy="191" r="18" fill="var(--forest)"/>
    <circle cx="736" cy="226" r="9" fill="var(--band)"/>
    <circle role="img" aria-label="Photo of Greek salad in a bowl" cx="546" cy="213" r="75" fill="url(#saladTone)"/>

    <ellipse role="img" aria-label="Photo of a kofta wrap" cx="535" cy="765" rx="105" ry="70" fill="url(#wrapTone)"/>

    <path role="img" aria-label="Photo of a mixed grill platter with rice" fill="url(#platterTone)"
      d="M600 849 C640 780 670 700 760 650 C860 600 1000 640 1100 620 C1150 610 1180 600 1200 595 V849 Z"/>
    <path fill="none" stroke="#fff" stroke-width="1.5" d="M660 849 C690 760 740 680 840 645 C960 610 1080 630 1200 600"/>
    <path fill="var(--forest)" d="M880 849 C960 790 1040 780 1110 760 C1160 745 1185 720 1200 710 V849 Z"/>
    <path fill="none" stroke="var(--amber)" stroke-width="3" d="M870 849 C950 785 1040 775 1110 755 C1160 740 1185 715 1200 705"/>
  </svg>

  <section class="column col-left">
    <h2 class="band">Sides</h2>
    <div class="list">
      <div class="item"><div class="item-head"><span class="item-name">Crispy French Fries</span><span class="leader"></span><span class="price">$ 2.00</span></div><p class="item-desc">Crispy Flavoured Frech Fries</p></div>
      <div class="item"><div class="item-head"><span class="item-name">French Fries</span><span class="leader"></span><span class="price">$ 1.75</span></div><p class="item-desc">Straight Cut Fries</p></div>
      <div class="item"><div class="item-head"><span class="item-name">Buffalo Chiken Wings 5 Pcs.</span><span class="leader"></span><span class="price">$ 5.50</span></div><p class="item-desc">Juicy from inside crispy from outside<br>for of flavours</p></div>
      <div class="item"><div class="item-head"><span class="item-name">Buffalo Chiken Wings 10 Pcs.</span><span class="leader"></span><span class="price">$ 10.00</span></div><p class="item-desc">Juicy from inside crispy from outside<br>for of flavours</p></div>
      <div class="item"><div class="item-head"><span class="item-name">Honey Garlic Chicken Wings</span><span class="leader"></span><span class="price">$ 10.00</span></div></div>
      <div class="item"><div class="item-head"><span class="item-name">Fried Calamari</span><span class="leader"></span><span class="price">$ 7.99</span></div></div>
      <div class="item"><div class="item-head"><span class="item-name">Oriental Rice</span><span class="leader"></span><span class="price">$ 2.00</span></div><p class="item-desc">Flavourful rice short grain rice cooked<br>with onion, garlic and tomato</p></div>
    </div>
    <h2 class="band wraps">Wraps</h2>
    <div class="list">
      <div class="item"><div class="item-head"><span class="item-name">Crispy Chicken</span><span class="leader"></span><span class="price">$ 6.99</span></div><p class="item-desc">Tender juicy peice of chicken marinated with our<br>im-house marination fried with a crispy tempura batter<br>serve with lettuce tomato cucumber pickles and mayo</p></div>
      <div class="item"><div class="item-head"><span class="item-name">Falafel</span><span class="leader"></span><span class="price">$ 4.99</span></div><p class="item-desc">Falafel is a deep-fried ball made from ground chickpeas<br>and fava beans. Served wrapped in a tortilla with<br>tahini sauce, lettuce, tomato and pickles</p></div>
      <div class="item"><div class="item-head"><span class="item-name">Grilled Chicken</span><span class="leader"></span><span class="price">$ 6.99</span></div><p class="item-desc">Tender juicy chicken pics marinated overnight was our<br>special marination made in the house laid over garlic<br>mayo lettuce and tomato and pickel wrap in tortilla</p></div>
      <div class="item"><div class="item-head"><span class="item-name">Kofta</span><span class="leader"></span><span class="price">$ 6.99</span></div><p class="item-desc">Barbeque ground beef our seasoning serve was the<br>tahini sauce pickle, lettuce and tomato</p></div>
    </div>
  </section>

  <section class="column col-mid">
    <h2 class="band">Salads</h2>
    <div class="list">
      <div class="item"><div class="item-head"><span class="item-name">Greek Salad</span><span class="leader"></span><span class="price">$ 6.99</span></div><p class="item-desc">Tomato, sliced cucumber, green pepper, sliced<br>red onion, kalamata olives and of course feta cheese.<br>It must be seasoned with dried oregano and saslt<br>and dressed with good quality extra virgin olive oil<br>and a splash of red wine vinger.</p></div>
      <div class="item"><div class="item-head"><span class="item-name">Mediterranean Salad</span><span class="leader"></span><span class="price">$ 6.99</span></div><p class="item-desc">Chickpeas and tomato, sliced cucumber, green<br>pepper, sliced red onion, Kalamata olives and<br>feta cheese. It seasoned with salt and pepper<br>and simple vinaigrette dressing.</p></div>
      <div class="item"><div class="item-head"><span class="item-name">Avocado Salad</span><span class="leader"></span><span class="price">$ 7.99</span></div><p class="item-desc">Avocado, tomato, sliced cucumber, green pepper, sliced<br>red onion and cliantro seasoning with simple vinaigrette.<br>(Extra virgin olive oil &amp; white win vinegar)</p></div>
      <div class="item"><div class="item-head"><span class="item-name">Caesar Salad</span><span class="leader"></span><span class="price">$ 6.99</span></div><p class="item-desc">Romaine lettuce and croutons dressed with<br>Caesar dressing, Parmesan cheese and black pepper.</p></div>
    </div>
  </section>

  <section class="column col-right">
    <h2 class="band">Soup</h2>
    <div class="list">
      <div class="item"><div class="item-head"><span class="item-name">Chicken Enchilada Soup</span><span class="leader"></span><span class="price">$ 4.99</span></div><p class="item-desc">Is creamy, rich, slightly spicy and thick blended<br>together and topped with shredded chicken breast.</p></div>
      <div class="item"><div class="item-head"><span class="item-name">Mediterranean Salad</span><span class="leader"></span><span class="price">$ 4.99</span></div><p class="item-desc">Creamy broth with roasted chicken and<br>garlicky mushrooms.</p></div>
      <div class="item"><div class="item-head"><span class="item-name">Lentils Salad</span><span class="leader"></span><span class="price">$ 4.99</span></div><p class="item-desc">It’s vegetarian soup made use mix brown, red, yellow<br>lentils cooked with carrot, tomato and onion making<br>a thick soup with hint of Cayenne pepper.</p></div>
      <div class="item"><div class="item-head"><span class="item-name">French Onion Soup</span><span class="leader"></span><span class="price">$ 4.99</span></div><p class="item-desc">Made with perfectly caramelized onions, fresh thyme<br>springs, crustly baguette slices of melted Gruyere cheese<br>right on top</p></div>
    </div>
    <h2 class="band platter">Platter</h2>
    <div class="list">
      <div class="item"><div class="item-head"><span class="item-name">Kofta Platter</span><span class="leader"></span><span class="price">$ 16.99</span></div><p class="item-desc">Two kofta skewers servers with oriental rice + salad<br>or french fries and 1 sauce</p></div>
      <div class="item"><div class="item-head"><span class="item-name">Friday Chicken Platter</span><span class="leader"></span><span class="price">$ 16.99</span></div><p class="item-desc">Two Friday chicken skewers servers with<br>oriental rice + salad or french fries and 1 sauce.</p></div>
      <div class="item"><div class="item-head"><span class="item-name">Grilled Chicken Platter</span><span class="leader"></span><span class="price">$ 16.99</span></div><p class="item-desc">Two pieces of grilled chicken thigh and breast servers<br>with oriental rice + salad or french fries and 1 sauce.</p></div>
      <div class="item"><div class="item-head"><span class="item-name">Mix Grilled Platter</span><span class="leader"></span><span class="price">$ 29.99</span></div><p class="item-desc">Two Friday chicken skewers + 2 skewers of kofta and<br>2 pieces of grilled chicken servers with oriental rice +<br>salad or french fries and 1 sauce.</p></div>
    </div>
  </section>
</main>
</body>
</html>
```